Brookvale Estates LLC stationary for a real estate property management company.

Create stationary (letterhead, envelopes, business cards) using Brookvale Estates LLC logo as primary creative element. Stationary design needs to be horizontal, leaving as much space as possible for correspondence copy. See attached Creative Brief and past stationary files for details.

Target Market(s)

Prospective apartment residents and current residents, vendors, and government agencies.

Industry/Entity Type

Property Management

Contact Information for Business Card

Business card employee title: Property Manager. Should include address, phone, fax, email, website, slogan, and Brookvale Estates logo.

Font styles to use
Sans Serif

Colors
0592cd
000000

Requirements
Must have
• Tone should be conservative, institutional, business (i.e. banking, finance, real estate). Must include: address, phone, fax, website, and slogan (see attached Creative Brief). Should be a horizontal design, leaving as much room as possible for letter correspondence copy.
Nice to have
• Please use an Arial or Helvetica style font.
Should not have
• Letterhead layout should leave as much room as possible for copy.

```html
<!DOCTYPE html>
<html lang="en">
<head>
<meta charset="utf-8">
<title>Brookvale Estates LLC – Business Card</title>
<link rel="stylesheet" href="https://fonts.googleapis.com/css2?family=Arimo:wght@400;700&display=swap">
<style>
  :root {
    --brand-blue: #0d67a5;
    --heading-blue: #1769ab;
    --text-grey: #555a5e;
    --rule-grey: #c9c9c9;
    --card-white: #f7f7f7;
    --backdrop: #e6e6e6;
    --white: #ffffff;
  }
  * { margin: 0; padding: 0; box-sizing: border-box; }
  html, body { width: 1200px; height: 960px; overflow: hidden; }
  body {
    position: relative;
    background: var(--backdrop);
    font-family: "Arimo", Arial, Helvetica, sans-serif;
  }
  .card {
    position: absolute;
    width: 600px;
    height: 342px;
  }
  .card--front { left: 302px; top: 130px; background: var(--card-white); }
  .card--back  { left: 299px; top: 488px; background: var(--brand-blue); }

  .brand {
    position: absolute;
    left: 0; right: 0; top: 108px;
    display: flex; align-items: center; justify-content: center; gap: 14px;
  }
  .brand__square { width: 30px; height: 30px; background: var(--brand-blue); }
  .brand__name {
    font-weight: 700; font-size: 34px; letter-spacing: 0.5px;
    color: var(--brand-blue);
  }

  .contact-person {
    position: absolute; right: 312px; top: 206px;
    text-align: right; color: var(--text-grey);
    font-size: 14px; line-height: 19px;
  }
  .contact-person__name {
    font-weight: 700; font-size: 21px; line-height: 26px;
    color: var(--heading-blue); letter-spacing: 0.2px;
  }
  .contact-person__title { font-size: 15px; line-height: 20px; }

  .divider {
    position: absolute; left: 305px; top: 208px;
    width: 1px; height: 80px; background: var(--rule-grey);
  }

  .contact-list {
    position: absolute; left: 322px; top: 209px;
    list-style: none; color: var(--text-grey);
    font-size: 14px; line-height: 19px;
  }
  .contact-list li { display: flex; align-items: center; gap: 9px; }
  .contact-list svg { width: 13px; height: 13px; fill: var(--brand-blue); flex: none; }

  .brand--reversed { top: 136px; flex-direction: column; gap: 22px; }
  .brand--reversed .brand__square { width: 48px; height: 48px; background: var(--white); }
  .brand--reversed .brand__name { color: var(--white); font-size: 36px; }

  .slogan {
    position: absolute; left: 0; right: 0; top: 287px;
    text-align: center; color: var(--white);
    font-weight: 700; font-size: 16px;
  }
</style>
</head>
<body>
  <section class="card card--front">
    <div class="brand">
      <span class="brand__square"></span>
      <span class="brand__name">BROOKVALE ESTATES LLC</span>
    </div>

    <div class="contact-person">
      <p class="contact-person__name">DANIEL HARTWELL</p>
      <p class="contact-person__title">Property Manager</p>
      <p>2750 Alder Creek Road #B210</p>
      <p>San Diego, CA 92108</p>
    </div>

    <div class="divider"></div>

    <ul class="contact-list">
      <li><svg viewBox="0 0 16 16"><path d="M3.5 1l2.6 3-1.5 1.8c.9 2 2.6 3.7 4.6 4.6L11 8.9l3 2.6-1.2 2.6C7 14.3 1.7 9 1.9 3.2z"/></svg>619-555-0142</li>
      <li><svg viewBox="0 0 16 16"><path d="M4 1h8v4H4zM1 6h14v6h-2v-2H3v2H1zM4 11h8v4H4z"/></svg>619-555-0187</li>
      <li><svg viewBox="0 0 16 16"><path d="M1 3h14v10H1zM2.3 4.2v.6L8 9l5.7-4.2v-.6z" fill-rule="evenodd"/></svg>daniel@brookvaleestates.us</li>
      <li><svg viewBox="0 0 16 16"><circle cx="8" cy="8" r="7"/></svg>www.brookvaleestates.us</li>
    </ul>
  </section>

  <section class="card card--back">
    <div class="brand brand--reversed">
      <span class="brand__square"></span>
      <span class="brand__name">BROOKVALE ESTATES</span>
    </div>
    <p class="slogan">Multifamily Property Management</p>
  </section>
</body>
</html>
```